L.U.M Ventures - Business Card

We need a business card design for a new company based in Malaysia, called L.U.M Ventures Sdn. Bhd. We create, develop & customize database & software/web-based business systems to suit our clients need, mainly in oil&gas industry.

We would like to challenge the creativity of you to design a simple, meaningful, modern, professional & sleek. The design concept may varies but worthy enough for the recipients to proudly keep it in their wallet, and award us with fruitful business opportunities.

B-3-12 Orchid Plaza,
JK9/4, Taman Melur,
43210 Selangor. Malaysia

http://lumventures-example.com

HAFIZ Kamaru | +6012-3817720 | Co-Founder
Ed Suhaimi | +6012-4093381 | Co-Founder
Abdul Nizam | +6019-5268149 | Managing Director

Target Market(s)

The target market will expand to several other industries such as aviation, communication, automotive, education & hotel.

Industry/Entity Type

Business

Font styles to use
Serif
Sans Serif
Decorative
Script

Requirements
Must have
• plain background yet colourful concept.
Should not have
• something too easy that I can draw myself

```html
<!DOCTYPE html>
<html lang="en">
<head>
<meta charset="utf-8">
<title>L.U.M Ventures – Business Card</title>
<link rel="stylesheet" href="https://fonts.googleapis.com/css2?family=Source+Sans+3:wght@400;600&display=swap">
<style>
  :root {
    --maroon: #4e0a1c;
    --maroon-dark: #3e0715;
    --band-grey: #e6e6e6;
    --paper: #ffffff;
    --gold: #f2a21c;
    --ink: #1e1e1e;
    --white: #ffffff;
    --rule: #8a5a62;
  }
  * { margin: 0; padding: 0; box-sizing: border-box; }
  html, body {
    width: 1200px; height: 683px; overflow: hidden;
    background: var(--paper);
    font-family: "Source Sans 3", "Myriad Pro", sans-serif;
  }
  .stage { position: relative; width: 1200px; height: 683px; }

  .stage-label {
    position: absolute; left: 670px; top: 0; width: 415px; height: 53px;
    background: var(--maroon); color: var(--white);
    font-size: 31px; font-weight: 400;
    display: flex; align-items: center; justify-content: center;
  }

  .card {
    position: absolute; left: 14px; top: 108px; width: 1140px; height: 531px;
    background: var(--maroon);
    box-shadow: 10px 10px 12px rgba(0,0,0,0.45);
  }
  .card-front {
    position: absolute; left: 0; top: 0; width: 100%; height: 361px;
  }
  .brand {
    position: absolute; left: 0; right: 0; top: 55px;
    display: flex; align-items: center; justify-content: center; gap: 34px;
  }
  .brand-name {
    color: var(--gold); font-weight: 600; font-size: 118px; line-height: 1;
    letter-spacing: 1px;
  }
  .brand-dot {
    width: 70px; height: 70px; border-radius: 50%; background: var(--gold);
  }
  .holder-name {
    position: absolute; left: 0; right: 0; top: 214px;
    text-align: center; color: var(--white); font-size: 38px; font-weight: 400;
  }
  .holder-rule {
    position: absolute; left: 393px; width: 328px; top: 267px;
    height: 1px; background: var(--rule);
  }
  .tagline {
    position: absolute; left: 0; right: 0; top: 280px;
    text-align: center; color: var(--white); font-size: 26px; font-weight: 400;
  }

  .contact-band {
    position: absolute; left: 0; top: 361px; width: 100%; height: 149px;
    background: var(--band-grey);
  }
  .contact-item {
    position: absolute; display: flex; align-items: center; gap: 8px;
    color: var(--ink); font-size: 21px;
  }
  .contact-item svg { display: block; }
  .contact-item.office  { left: 111px; top: 22px; }
  .contact-item.phone   { left: 111px; top: 66px; }
  .contact-item.website { left: 639px; top: 17px; }
  .contact-item.email   { left: 648px; top: 66px; }
</style>
</head>
<body>
<main class="stage">
  <div class="stage-label">Proposed design</div>

  <section class="card" aria-label="L.U.M Ventures business card">
    <div class="card-front">
      <div class="brand">
        <span class="brand-name">L.U.M</span>
        <span class="brand-dot" aria-hidden="true"></span>
      </div>
      <h1 class="holder-name">NAME</h1>
      <div class="holder-rule"></div>
      <p class="tagline">We provide data intelligence &amp; analytic solution especially in the oil &amp; gas industry</p>
    </div>

    <div class="contact-band">
      <div class="contact-item office">
        <svg width="58" height="30" viewBox="0 0 58 30" aria-hidden="true">
          <path d="M2 15 L29 1 L56 15 L51 17 L29 6 L7 17 Z" fill="var(--maroon)"/>
          <path d="M12 16 L29 8 L46 16 L46 29 L34 29 L34 20 L24 20 L24 29 L12 29 Z" fill="var(--maroon)"/>
        </svg>
        <span>Office location</span>
      </div>
      <div class="contact-item phone">
        <svg width="58" height="28" viewBox="0 0 58 28" aria-hidden="true">
          <path d="M4 22 C2 17 8 13 14 16 L20 18 C30 14 38 9 44 5 L46 0 C52 -1 57 4 54 8 C48 15 30 26 12 27 C7 27 5 25 4 22 Z" fill="var(--maroon)"/>
        </svg>
        <span>Contact number</span>
      </div>
      <div class="contact-item website">
        <svg width="52" height="38" viewBox="0 0 52 38" aria-hidden="true">
          <rect x="1.5" y="1.5" width="49" height="35" fill="none" stroke="var(--maroon)" stroke-width="2.5"/>
          <ellipse cx="26" cy="19" rx="17" ry="11" fill="none" stroke="var(--maroon)" stroke-width="2.5"/>
          <ellipse cx="26" cy="19" rx="7" ry="11" fill="none" stroke="var(--maroon)" stroke-width="2"/>
          <line x1="9" y1="19" x2="43" y2="19" stroke="var(--maroon)" stroke-width="2"/>
          <line x1="12" y1="13" x2="40" y2="13" stroke="var(--maroon)" stroke-width="1.5"/>
          <line x1="12" y1="25" x2="40" y2="25" stroke="var(--maroon)" stroke-width="1.5"/>
        </svg>
        <span>Website domain name</span>
      </div>
      <div class="contact-item email">
        <svg width="46" height="26" viewBox="0 0 46 26" aria-hidden="true">
          <rect x="0" y="0" width="46" height="26" rx="3" fill="var(--maroon)"/>
          <path d="M3 3 L23 16 L43 3" fill="none" stroke="var(--band-grey)" stroke-width="2"/>
          <path d="M3 23 L17 12 M43 23 L29 12" stroke="var(--band-grey)" stroke-width="1.5"/>
        </svg>
        <span>Email address</span>
      </div>
    </div>
  </section>
</main>
</body>
</html>
```